Request for Business Card Design

Hi. My name is Marlene, I am looking for a new business card design for my company, Quarrow Signal Instruments, LLC. I really like the design you did for Tarsel Venture and was hoping you could do something similar using our full logo and our mark. I am also open to any raised texture design using our mark. I have attached our full logo, which would need to be somewhere on the card, as well as the mark in both outline and full form, as well as our brand colors / guide. The card does not have to be white, as long as our logo and mark appear. I actually like darker colored business cards more, but am open to all options. If you are interested in working with me, please let me know. We would also take the business card design into letterhead design if you can do that.

```html
<!DOCTYPE html>
<html lang="en">
<head>
<meta charset="utf-8">
<title>Quarrow Signal Instruments — Business Card</title>
<link href="https://fonts.googleapis.com/css2?family=Montserrat:wght@400;500;600&display=swap" rel="stylesheet">
<style>
  :root {
    --backdrop: #2a2a2c;
    --card: #0d0d0e;
    --brand-blue: #1a9fce;
    --text-light: #f2f2f2;
    --text-muted: #c9c9c9;
    --divider: #555558;
    --silver: #e4e4e4;
  }
  * { box-sizing: border-box; margin: 0; padding: 0; }
  html, body {
    width: 1200px; height: 900px; overflow: hidden;
    background: var(--backdrop);
    font-family: "Montserrat", sans-serif;
  }
  .canvas {
    width: 1200px; height: 900px;
    display: flex; flex-direction: column; align-items: center; justify-content: center;
    gap: 56px;
  }
  .card {
    width: 660px; height: 377px;
    background: var(--card);
    border-radius: 26px;
    position: relative;
    overflow: hidden;
  }
  /* Front */
  .card--front { display: flex; align-items: center; }
  .front-brand {
    width: 310px; padding-left: 48px; padding-right: 24px;
    display: flex; flex-direction: column; align-items: flex-start; gap: 18px;
  }
  .brand-dot {
    width: 62px; height: 62px; border-radius: 50%;
    background: var(--brand-blue);
  }
  .brand-name {
    color: var(--text-light);
    font-weight: 600;
    text-transform: uppercase;
    line-height: 1.15;
    white-space: nowrap;
  }
  .brand-name .primary { display: block; font-size: 34px; letter-spacing: 4px; }
  .brand-name .secondary { display: block; font-size: 11px; letter-spacing: 1px; }
  .front-divider {
    width: 1px; height: 170px; background: var(--divider);
    margin-right: 34px; flex-shrink: 0;
  }
  .contact { color: var(--text-muted); }
  .contact-name {
    color: var(--brand-blue); font-size: 20px; font-weight: 500;
    letter-spacing: 0.5px; text-transform: uppercase;
  }
  .contact-title { font-size: 14px; margin-bottom: 14px; }
  .contact-list { list-style: none; font-size: 14px; line-height: 1.6; }
  .contact-list li { display: flex; align-items: center; gap: 8px; }
  .contact-list svg { width: 13px; height: 13px; flex-shrink: 0; }
  .contact-address { font-size: 14px; line-height: 1.5; margin-top: 12px; }
  /* Back */
  .card--back { display: flex; align-items: center; justify-content: center; gap: 22px; }
  .card--back .brand-dot { background: var(--silver); width: 70px; height: 70px; }
  .card--back .brand-name { color: var(--silver); }
  .card--back .brand-name .primary { font-size: 38px; letter-spacing: 5px; }
</style>
</head>
<body>
<main class="canvas">
  <section class="card card--front">
    <div class="front-brand">
      <span class="brand-dot"></span>
      <div class="brand-name"><span class="primary">Quarrow</span><span class="secondary">Signal Instruments</span></div>
    </div>
    <div class="front-divider"></div>
    <div class="contact">
      <h1 class="contact-name">Marlene Holt</h1>
      <p class="contact-title">Managing Director</p>
      <ul class="contact-list">
        <li><svg viewBox="0 0 16 16" aria-hidden="true"><path fill="#1a9fce" d="M3.5 1.5l2.5 0.5 1 3-1.6 1.2a8 8 0 0 0 4.4 4.4L11 9l3 1 0.5 2.5-2 2C7 14 2 9 1.5 3.5z"/></svg>071-380 552 146</li>
        <li><svg viewBox="0 0 16 16" aria-hidden="true"><rect x="1" y="3.5" width="14" height="9" fill="#1a9fce"/><path d="M1 3.5l7 5 7-5" stroke="#0d0d0e" stroke-width="1.3" fill="none"/></svg>info@quarrowsignal.com</li>
        <li><svg viewBox="0 0 16 16" aria-hidden="true"><circle cx="8" cy="8" r="6.5" fill="none" stroke="#1a9fce" stroke-width="1.5"/><path d="M1.5 8h13M8 1.5c-3 3.5-3 9.5 0 13M8 1.5c3 3.5 3 9.5 0 13" stroke="#1a9fce" stroke-width="1.2" fill="none"/></svg>www.quarrowsignal.com</li>
      </ul>
      <p class="contact-address">87, Fenmoor Road, Ashgate<br>30918, Northland</p>
    </div>
  </section>
  <section class="card card--back">
    <span class="brand-dot"></span>
    <div class="brand-name"><span class="primary">Quarrow</span><span class="secondary">Signal Instruments</span></div>
  </section>
</main>
</body>
</html>
```